Communication and Marketing agency needs a new presentation card

We are a group of communication and marketing agencies specialized in companies that are in the logistics and industrial sector. The head agency is TELVANO Grupo and the group consists of 4 agencies: TELVANO Media, TELVANO Digital, TELVANO Research and DifundeEnPantalla. We hace 4 offices in Spain (Madrid, Barcelona, Valencia and Murcia). We are looking for a clean and attractive design that transmits our experience, brand presence in the market and knowledge to those who receive the card.It has to maintain the colors of the logo that is attached.
Target Market(s)
logistics and industrial sector
Marketing department
Contact Information for Business Card
Clean and attractive design

```html
<!DOCTYPE html>
<html lang="en">
<head>
<meta charset="utf-8">
<title>TELVANO Grupo – Business Card</title>
<link rel="stylesheet" href="https://fonts.googleapis.com/css2?family=Open+Sans:wght@400;600;700&family=Oswald:wght@600&display=swap">
<style>
  :root {
    --brand-red: #b51f2a;
    --card-black: #1b1b1c;
    --card-white: #ffffff;
    --text-grey: #4a4a4a;
    --backdrop: #e9e7e4;
  }
  * { margin: 0; padding: 0; box-sizing: border-box; }
  html, body {
    width: 1200px;
    height: 971px;
    overflow: hidden;
    background: var(--backdrop);
    font-family: "Open Sans", Arial, sans-serif;
  }
  .card {
    position: absolute;
    left: 250px;
    width: 700px;
    height: 400px;
    overflow: hidden;
    box-shadow: 0 6px 18px rgba(0,0,0,0.18);
  }
  .card--front { top: 55px; background: var(--card-black); }
  .card--back  { top: 516px; background: var(--card-white); }

  .brand-name {
    font-family: "Open Sans", Arial, sans-serif;
    font-weight: 700;
    color: var(--brand-red);
    white-space: nowrap;
    letter-spacing: 1px;
  }
  .card--front .brand-name {
    position: absolute;
    left: 0; right: 0;
    top: 168px;
    text-align: center;
    font-size: 52px;
  }
  .card--back .brand-name {
    position: absolute;
    left: 46px;
    top: 36px;
    font-size: 30px;
  }

  .person {
    position: absolute;
    left: 70px;
    top: 190px;
  }
  .person__name {
    font-family: "Oswald", "Arial Narrow", sans-serif;
    font-weight: 600;
    font-size: 30px;
    letter-spacing: 1px;
    color: var(--brand-red);
    line-height: 1.1;
  }
  .person__role {
    font-size: 20px;
    color: var(--text-grey);
    line-height: 1.2;
  }
  .divider {
    position: absolute;
    left: 70px;
    top: 268px;
    width: 590px;
    height: 1.5px;
    background: var(--brand-red);
  }
  .contact {
    position: absolute;
    left: 70px;
    top: 282px;
    list-style: none;
    font-size: 17px;
    color: var(--text-grey);
    line-height: 1.5;
  }
  .contact li { display: flex; align-items: center; gap: 8px; }
  .contact svg { width: 13px; height: 13px; fill: var(--brand-red); }
  .address {
    position: absolute;
    right: 40px;
    top: 226px;
    text-align: right;
    font-size: 16px;
    color: var(--text-grey);
    line-height: 1.35;
    font-style: normal;
  }
  .footer-wave {
    position: absolute;
    left: 0; top: 0;
    width: 700px; height: 400px;
  }
  .website {
    position: absolute;
    right: 40px;
    top: 340px;
    font-size: 17px;
    color: var(--card-white);
  }
  .website strong { color: var(--brand-red); font-weight: 700; }
</style>
</head>
<body>

<section class="card card--front" aria-label="Card front">
  <div class="brand-name">TELVANO Grupo</div>
</section>

<section class="card card--back" aria-label="Card back">
  <svg class="footer-wave" viewBox="0 0 700 400" aria-hidden="true">
    <path d="M0,340 C150,392 300,372 450,332 C550,305 620,302 700,304 L700,400 L0,400 Z" fill="var(--card-black)"/>
    <path d="M110,378 C260,368 390,338 470,318 C560,294 625,289 690,290" fill="none" stroke="var(--brand-red)" stroke-width="7" stroke-linecap="round"/>
  </svg>

  <div class="brand-name">TELVANO Grupo</div>

  <div class="person">
    <div class="person__name">ADRIAN VELA</div>
    <div class="person__role">Founder</div>
  </div>

  <address class="address">214 Calle Alameda,<br>28014 Madrid, Spain</address>

  <div class="divider"></div>

  <ul class="contact">
    <li>
      <svg viewBox="0 0 24 24" aria-hidden="true"><path d="M6.6 10.8a15.1 15.1 0 0 0 6.6 6.6l2.2-2.2a1 1 0 0 1 1-.25 11.4 11.4 0 0 0 3.6.57 1 1 0 0 1 1 1V20a1 1 0 0 1-1 1A17 17 0 0 1 3 4a1 1 0 0 1 1-1h3.5a1 1 0 0 1 1 1c0 1.25.2 2.45.57 3.57a1 1 0 0 1-.25 1z"/></svg>
      (000) 987-654-00
    </li>
    <li>
      <svg viewBox="0 0 24 24" aria-hidden="true"><path d="M2 5h20v14H2z M2 5l10 8 10-8" fill="var(--brand-red)"/><path d="M2 6l10 7.5L22 6" fill="none" stroke="#fff" stroke-width="1.8"/></svg>
      info@telvanogrupo.com
    </li>
  </ul>

  <div class="website">www.<strong>telvanogrupo</strong>.com</div>
</section>

</body>
</html>
```